We are a local Communty Pharmacy wishing to promote and market a specialised Pharmaceutical Service

We would like a design that is professional and enticing ( according to the brief In attached files)
We wish to Market Compounding Pharmacy as a specialist side of our business.
We have the expertise a purpose built preparation laboratory.
The main purpose is an Internet presence that entices prospective patients to contact or visit our physical store.

Target Market(s)

Patients Medicos and Veterinary clients

Industry/Entity Type

Pharmacy

Coding

Coded - Design and coding required

Number of Pages Required

1 page

Requirements
Must have
• Clear friendly image
Nice to have
• soft enticing feel
Should not have
• No crass loud unprofessional elements

```html
<!DOCTYPE html>
<html lang="en">
<head>
<meta charset="utf-8">
<title>Willowbend Pharmacy – Compounding</title>
<link href="https://fonts.googleapis.com/css2?family=Open+Sans:wght@400;600;700;800&family=Oswald:wght@500;600&display=swap" rel="stylesheet">
<style>
:root{
  --blue:#1f7fc4;
  --blue-dark:#0f5f9c;
  --sky:#d9ecf8;
  --yellow:#f2b51c;
  --ink:#3a3a3a;
  --muted:#6b6b6b;
  --footer:#3c4650;
  --footer-dark:#2c343c;
  --white:#ffffff;
}
*{box-sizing:border-box;margin:0;padding:0}
html,body{width:673px;height:1200px;overflow:hidden;background:var(--white)}
body{font-family:"Open Sans",Arial,sans-serif;color:var(--ink);position:relative}
.topbar{height:74px;display:flex;justify-content:space-between;align-items:center;padding:0 30px}
.brand{display:flex;align-items:center;gap:8px}
.brand-mark{width:30px;height:30px;background:var(--blue);border-radius:50%}
.brand-name{font-weight:800;font-size:17px;color:var(--blue-dark);letter-spacing:.5px}
.contact-top{font-size:7px;color:var(--muted);line-height:1.7}
.contact-top strong{display:block;font-size:8px;color:var(--ink)}
.contact-top .row{display:flex;gap:16px}
.nav{height:27px;background:linear-gradient(var(--blue),var(--blue-dark));display:flex;padding-left:70px}
.nav a{color:var(--white);font-size:7.5px;font-weight:700;text-decoration:none;width:76px;display:flex;align-items:center;justify-content:center;letter-spacing:.5px}
.nav a.active{background:var(--yellow)}
.hero{position:relative;height:314px}
.hero-photo{position:absolute;inset:0;background:linear-gradient(100deg,#bcd6e6 0%,#e8f1f6 45%,#f6f9fb 100%)}
.hero-copy{position:absolute;left:300px;top:115px}
.hero-title{font-family:"Oswald",sans-serif;font-size:27px;color:var(--blue);letter-spacing:.5px}
.hero-sub{display:inline-block;background:var(--blue);color:var(--white);font-family:"Oswald",sans-serif;font-size:15px;padding:2px 8px;margin-top:2px}
.hero-btn{display:inline-block;margin-top:14px;background:var(--yellow);color:var(--white);font-size:7px;font-weight:700;padding:6px 12px}
.hero-arrow{position:absolute;top:142px;width:20px;height:20px;border-radius:50%;background:rgba(80,80,80,.5)}
.hero-arrow.l{left:20px}.hero-arrow.r{right:20px}
.intro{padding:22px 40px 0;text-align:center}
.section-title{font-size:15px;font-weight:800;color:var(--blue-dark);margin-bottom:14px}
.intro p{font-size:6.6px;line-height:1.75;color:var(--muted);margin-bottom:10px}
.values{display:flex;justify-content:space-around;padding:6px 30px 0}
.value{width:110px;text-align:center}
.value-icon{width:62px;height:62px;border-radius:50%;background:var(--blue);margin:0 auto 10px;display:flex;align-items:center;justify-content:center}
.value h4{font-size:7.5px;font-weight:800;color:var(--ink);line-height:1.35}
.features{padding-top:26px;text-align:center}
.features .section-title{font-size:17px;color:var(--ink);display:flex;align-items:center;justify-content:center;gap:14px}
.features .section-title::before,.features .section-title::after{content:"";width:170px;height:1px;background:#ccc}
.cards{display:flex;justify-content:space-between;padding:0 40px;text-align:left}
.card{width:175px}
.card-photo{height:78px;margin-bottom:8px}
.card h5{font-size:8px;font-weight:700;margin-bottom:3px}
.card p{font-size:6.5px;line-height:1.6;color:var(--muted)}
.card .more{font-size:6.5px;font-weight:700;color:var(--yellow);margin-top:4px}
.pager{display:flex;justify-content:center;gap:6px;margin-top:12px}
.pager span{width:13px;height:13px;border-radius:50%;background:#bbb}
.footer{position:absolute;left:0;right:0;top:1010px;height:135px;background:var(--footer);display:flex;padding:16px 40px;gap:30px;color:#d6dbe0}
.footer-col{flex:1}
.footer-col h6{font-size:10px;color:var(--white);display:flex;align-items:center;gap:6px;margin-bottom:10px}
.footer-col .row{display:flex;justify-content:space-between;font-size:6.5px;line-height:2.2}
.footer-col .line{font-size:6.5px;line-height:1.9}
.map-box{height:80px;background:#4c5761}
.bottom-bar{position:absolute;left:0;right:0;top:1145px;height:33px;background:var(--yellow);display:flex;align-items:center;justify-content:space-between;padding:0 40px}
.bottom-links{display:flex;gap:12px;font-size:6.5px;color:var(--white)}
.socials{display:flex;gap:6px}
.socials span{width:15px;height:15px;background:var(--white);opacity:.9}
.copyright{position:absolute;left:0;right:0;top:1178px;height:22px;background:var(--footer-dark);color:#aeb6be;font-size:6px;display:flex;align-items:center;padding-left:40px}
</style>
</head>
<body>
<header class="topbar">
  <div class="brand"><span class="brand-mark"></span><span class="brand-name">WILLOWBEND PHARMACY</span></div>
  <div class="contact-top">
    <strong>Contact us :</strong>
    <div class="row"><span>14 Harlow Crescent</span><span>08 5550 1427</span></div>
    <div class="row"><span>Fernvale WA 6100</span><span>care@willowbendpharmacy.example</span></div>
  </div>
</header>
<nav class="nav">
  <a class="active">HOME</a><a>ABOUT US</a><a>SERVICES</a><a>PRODUCTS</a><a>NEWS</a><a>LINKS</a><a>CONTACTS</a>
</nav>
<section class="hero">
  <div class="hero-photo" role="img" aria-label="Laboratory photograph with a microscope and glassware in soft blue light"></div>
  <div class="hero-copy">
    <div class="hero-title">COMPOUNDING PHARMACY</div>
    <div class="hero-sub">IS CUSTOMISED MEDICATIONS FOR PATIENTS</div><br>
    <span class="hero-btn">GET MORE INFO</span>
  </div>
  <span class="hero-arrow l"></span><span class="hero-arrow r"></span>
</section>
<section class="intro">
  <h2 class="section-title">WHAT IS COMPOUNDING PHARMACY?</h2>
  <p>Compounding is the art and science of preparing personalised medicines for patients. Long before mass manufacturing, almost every prescription was prepared by a pharmacist. Today compounding returns to meet needs that standard products cannot serve, such as removing an allergen, changing a dose strength, or turning a tablet into a liquid, cream or flavoured form that is easier to take for children, older people and animals.</p>
  <p>Our pharmacists work closely with doctors, veterinarians and patients to prepare each formula in our purpose built laboratory. Every preparation follows strict quality procedures, using pharmaceutical grade ingredients, calibrated equipment and careful documentation, so that every patient receives a safe and consistent medicine made for them alone.</p>
  <p>Willowbend Pharmacy has invested in training, equipment and a dedicated compounding room to offer this specialist service to our local community. Visit our store or contact our team to discuss how a customised medication could help you, your family or your animals, and let us work with your prescriber to find the right solution for your needs.</p>
</section>
<section class="values">
  <div class="value"><div class="value-icon"><svg width="28" height="28" viewBox="0 0 28 28" fill="none" stroke="#fff" stroke-width="2"><path d="M4 8h8v14H4zM16 8h8v14h-8z"/></svg></div><h4>KNOWLEDGE AND SKILLS UPDATING</h4></div>
  <div class="value"><div class="value-icon"><svg width="28" height="28" viewBox="0 0 28 28" fill="none" stroke="#fff" stroke-width="2"><circle cx="14" cy="11" r="7"/><path d="M10 17l-2 8 6-3 6 3-2-8"/></svg></div><h4>HIGHEST STANDARDS</h4></div>
  <div class="value"><div class="value-icon"><svg width="28" height="28" viewBox="0 0 28 28" fill="none" stroke="#fff" stroke-width="2"><path d="M5 14l6 6 12-12"/></svg></div><h4>QUALITY OF SERVICE</h4></div>
  <div class="value"><div class="value-icon"><svg width="28" height="28" viewBox="0 0 28 28" fill="none" stroke="#fff" stroke-width="2"><path d="M14 24s-9-6-9-12a5 5 0 0 1 9-3 5 5 0 0 1 9 3c0 6-9 12-9 12z"/></svg></div><h4>SUPPORT AN EFFECTIVE &amp; COMPETENT PRACTICE</h4></div>
  <div class="value"><div class="value-icon"><svg width="28" height="28" viewBox="0 0 28 28" fill="none" stroke="#fff" stroke-width="2"><circle cx="14" cy="14" r="9"/><circle cx="14" cy="14" r="4"/></svg></div><h4>OUR ULTIMATE GOAL</h4></div>
</section>
<section class="features">
  <h2 class="section-title">Feature Items</h2>
  <div class="cards">
    <div class="card"><div class="card-photo" role="img" aria-label="Photograph of a veterinarian examining a pet" style="background:linear-gradient(135deg,#c9dbe6,#eef3f6)"></div><h5>Vet Article</h5><p>Personalised medicines for animals, prepared in flavours and doses that pets will accept more easily…</p><div class="more">READ MORE »</div></div>
    <div class="card"><div class="card-photo" role="img" aria-label="Photograph of a patient receiving dental care" style="background:linear-gradient(135deg,#9fd0e6,#e3f1f8)"></div><h5>Scar Therapy</h5><p>Custom topical preparations designed with your prescriber to support healing and skin recovery…</p><div class="more">READ MORE »</div></div>
    <div class="card"><div class="card-photo" role="img" aria-label="Photograph of a patient having a thyroid check" style="background:linear-gradient(135deg,#b8d3e3,#edf4f8)"></div><h5>Thyroid Extract</h5><p>Tailored thyroid formulations prepared to the exact strength your doctor prescribes for you…</p><div class="more">READ MORE »</div></div>
  </div>
  <div class="pager"><span></span><span></span></div>
</section>
<footer class="footer">
  <div class="footer-col">
    <h6><svg width="12" height="12" viewBox="0 0 12 12" fill="none" stroke="#fff" stroke-width="1.5"><circle cx="6" cy="6" r="5"/><path d="M6 3v3l2 1"/></svg>Working Hours</h6>
    <div class="row"><span>Sunday</span><span>8.30 AM TO 6.30 PM</span></div>
    <div class="row"><span>Monday - Friday</span><span>8.30 AM TO 8.30 PM</span></div>
    <div class="row"><span>Saturday</span><span>8.30 AM TO 6.30 PM</span></div>
  </div>
  <div class="footer-col">
    <h6><svg width="12" height="12" viewBox="0 0 12 12" fill="#fff"><path d="M6 1a3.5 3.5 0 0 0-3.5 3.5C2.5 7 6 11 6 11s3.5-4 3.5-6.5A3.5 3.5 0 0 0 6 1z"/></svg>Location</h6>
    <div class="map-box" role="img" aria-label="Street map showing the pharmacy location"></div>
  </div>
  <div class="footer-col">
    <h6><svg width="12" height="12" viewBox="0 0 12 12" fill="#fff"><path d="M2 1h3l1 3-2 1a7 7 0 0 0 3 3l1-2 3 1v3a1 1 0 0 1-1 1A10 10 0 0 1 1 2a1 1 0 0 1 1-1z"/></svg>Contact Us</h6>
    <div class="line">14 Harlow Crescent<br>Fernvale WA 6100<br>Western Australia</div>
    <div class="line">08 5550 1427<br>08 5550 1428<br>care@willowbendpharmacy.example</div>
  </div>
</footer>
<div class="bottom-bar">
  <div class="bottom-links"><span>Home</span><span>About Us</span><span>Services</span><span>Products</span><span>News</span><span>Links</span><span>Contacts</span></div>
  <div class="socials"><span></span><span></span><span></span><span></span><span></span></div>
</div>
<div class="copyright">Copyright © Willowbend Pharmacy. All Rights Reserved.</div>
</body>
</html>
```